Water, flood Fire mold Damage Restoration Specialists

We want a well designed brochure- reflecting our company based values of integrity,expertise & reliability. services & testimonials. Logo driven. 1 professional referral based informative ("why choose Tovin Crest") design (plumbers, insurance adjusters, property managers, realitors,etc)
And one informative residential/commercial property owner design- what to expect when you hire Tovin Crest professionals

Industry/Entity Type

It Company

Font styles to use
Serif
Other font styles liked:
• Times Bold

Requirements
Must have
• A great flow, tri fold, color match from logo and wrapped vehicles. We handle insurance claims using insurance software called "xactimate" - ensuring claims are 100% expert driven

```html
<!DOCTYPE html>
<html lang="en">
<head>
<meta charset="utf-8">
<title>Tovin Crest Tri-fold Brochure – Outside Spread</title>
<link href="https://fonts.googleapis.com/css2?family=Roboto+Condensed:wght@400;700;900&family=Open+Sans:wght@400;600;700&display=swap" rel="stylesheet">
<style>
  :root{
    --blue-deep:#163f8a;
    --blue:#2360c4;
    --blue-light:#3f86e0;
    --red:#d3232a;
    --ink:#2b2f38;
    --muted:#6b7280;
    --paper:#ffffff;
    --stage:#eceef1;
  }
  *{box-sizing:border-box;margin:0;padding:0}
  html,body{width:889px;height:1200px;overflow:hidden;background:var(--stage)}
  body{font-family:"Open Sans",Arial,sans-serif;color:var(--ink)}
  .spread{position:absolute;left:20px;top:272px;width:849px;height:656px;background:var(--paper);display:flex;box-shadow:0 4px 16px rgba(0,0,0,.15)}
  .panel{position:relative;width:283px;height:100%;overflow:hidden}
  .panel + .panel{border-left:1px solid #e3e6ea}
  h2{font-family:"Roboto Condensed",Arial,sans-serif;font-weight:900;font-size:24px;letter-spacing:.5px;text-transform:uppercase}
  .red{color:var(--red)} .blue{color:var(--blue)}

  /* services panel */
  .services{padding:34px 28px 0}
  .service-list{list-style:none;margin-top:18px}
  .service-list li{display:flex;align-items:center;gap:12px;font-size:13px;font-weight:600;margin-bottom:13px}
  .icon-dot{width:26px;height:26px;border-radius:50%;background:var(--blue);display:flex;align-items:center;justify-content:center;flex:none}
  .deductible{position:absolute;left:24px;top:340px;width:104px;background:var(--red);color:#fff;text-align:center;padding:8px 4px;font-family:"Roboto Condensed",Arial,sans-serif;z-index:2}
  .deductible .small{font-size:10px;font-weight:700;text-transform:uppercase;line-height:1.2}
  .deductible .amount{font-size:34px;font-weight:900;line-height:1.05}
  .van-photo{position:absolute;left:0;bottom:0;width:100%;height:300px;background:linear-gradient(160deg,#d7dde6 0%,#8aa3c8 45%,#2d5fb0 100%)}

  /* why panel */
  .why{padding:34px 24px 0}
  .bullets{list-style:none;font-size:11px;color:var(--muted);line-height:1.5}
  .bullets li::before{content:"\25A0";color:var(--blue);font-size:8px;margin-right:7px;vertical-align:1px}
  .why h2{margin-top:20px;text-align:center}
  .why h2 span{color:var(--red)}
  .reasons{display:grid;grid-template-columns:1fr 1fr;gap:18px 10px;margin-top:18px}
  .reason{text-align:center;font-size:11px;font-weight:600;line-height:1.3}
  .reason .icon-dot{width:48px;height:48px;margin:0 auto 7px;background:var(--blue-deep)}
  .follow{margin-top:22px;display:flex;align-items:center;gap:7px;font-family:"Roboto Condensed",Arial,sans-serif;font-weight:700;font-size:13px;color:var(--blue-deep);text-transform:uppercase}
  .social{width:20px;height:20px;border-radius:50%;background:var(--blue)}
  .contact{position:absolute;left:0;right:0;bottom:26px;text-align:center}
  .contact .note{font-size:10px;color:var(--muted);line-height:1.35}
  .contact .phone{font-family:"Roboto Condensed",Arial,sans-serif;font-weight:900;font-size:30px;color:var(--blue-deep);margin-top:6px}
  .contact .web{font-size:12px;font-weight:600;color:var(--blue)}

  /* cover panel */
  .cover-photo{position:absolute;left:0;top:0;width:100%;height:360px;background:linear-gradient(150deg,#caa27a 0%,#8d6a4c 50%,#e9e6e0 100%)}
  .cover-band{position:absolute;left:0;top:0;width:100%;height:100%}
  .cover-title{position:absolute;right:20px;top:342px;width:220px;text-align:right;color:#fff;font-family:"Roboto Condensed",Arial,sans-serif;font-weight:900;font-size:25px;line-height:1.08;text-transform:uppercase}
  .brand{position:absolute;left:0;right:0;bottom:30px;text-align:center}
  .brand-name{display:inline-flex;align-items:center;gap:8px;font-family:"Roboto Condensed",Arial,sans-serif;font-weight:900;font-size:32px;color:var(--blue-deep);text-transform:uppercase}
  .brand-mark{width:14px;height:14px;border-radius:50%;background:var(--red)}
  .brand-tag{font-size:11px;color:var(--muted);margin-top:2px}
  .brand-web{font-size:12px;font-weight:600;color:var(--blue);margin-top:10px}
</style>
</head>
<body>
<main class="spread">

  <section class="panel services">
    <h2 class="red">Our Services</h2>
    <ul class="service-list">
      <li><span class="icon-dot"><svg width="14" height="14" viewBox="0 0 14 14"><path d="M3 7.5l2.5 2.5L11 4" stroke="#fff" stroke-width="2" fill="none"/></svg></span>Water Damage Restoration</li>
      <li><span class="icon-dot"><svg width="14" height="14" viewBox="0 0 14 14"><path d="M3 7.5l2.5 2.5L11 4" stroke="#fff" stroke-width="2" fill="none"/></svg></span>Fire &amp; Smoke Damage</li>
      <li><span class="icon-dot"><svg width="14" height="14" viewBox="0 0 14 14"><path d="M3 7.5l2.5 2.5L11 4" stroke="#fff" stroke-width="2" fill="none"/></svg></span>Mold Removal</li>
      <li><span class="icon-dot"><svg width="14" height="14" viewBox="0 0 14 14"><path d="M3 7.5l2.5 2.5L11 4" stroke="#fff" stroke-width="2" fill="none"/></svg></span>Sewage Cleanup</li>
      <li><span class="icon-dot"><svg width="14" height="14" viewBox="0 0 14 14"><path d="M3 7.5l2.5 2.5L11 4" stroke="#fff" stroke-width="2" fill="none"/></svg></span>Content PackOut</li>
      <li><span class="icon-dot"><svg width="14" height="14" viewBox="0 0 14 14"><path d="M3 7.5l2.5 2.5L11 4" stroke="#fff" stroke-width="2" fill="none"/></svg></span>Reconstruction</li>
    </ul>
    <div class="deductible">
      <div class="small">We will pay up to</div>
      <div class="amount">$500</div>
      <div class="small">of your deductible</div>
    </div>
    <div class="van-photo" role="img" aria-label="Photo of the company's wrapped blue service van"></div>
  </section>

  <section class="panel why">
    <ul class="bullets">
      <li>Direct billing to your insurance</li>
      <li>Free estimates</li>
      <li>We work with all insurers</li>
      <li>Certified, insured technicians</li>
      <li>Locally owned and operated</li>
    </ul>
    <h2 class="blue">Why <span>Choose</span> Us?</h2>
    <div class="reasons">
      <div class="reason"><span class="icon-dot"><svg width="24" height="24" viewBox="0 0 24 24"><path d="M5 12.5l4.5 4.5L19 7" stroke="#fff" stroke-width="2.6" fill="none"/></svg></span>100% Satisfaction</div>
      <div class="reason"><span class="icon-dot"><svg width="24" height="24" viewBox="0 0 24 24"><circle cx="12" cy="12" r="8" stroke="#fff" stroke-width="2" fill="none"/><path d="M12 7v5l3 2" stroke="#fff" stroke-width="2" fill="none"/></svg></span>On-time Service</div>
      <div class="reason"><span class="icon-dot"><svg width="24" height="24" viewBox="0 0 24 24"><circle cx="12" cy="8" r="4" fill="#fff"/><path d="M4 20c1-4 4-6 8-6s7 2 8 6z" fill="#fff"/></svg></span>Experienced Technicians</div>
      <div class="reason"><span class="icon-dot"><svg width="24" height="24" viewBox="0 0 24 24"><path d="M12 3l2.6 5.6 6 .7-4.5 4.1 1.2 6L12 16.5 6.7 19.4l1.2-6L3.4 9.3l6-.7z" fill="#fff"/></svg></span>Professionalism</div>
    </div>
    <div class="follow">Follow us on <span class="social"></span><span class="social"></span><span class="social"></span></div>
    <div class="contact">
      <div class="note">Day Or Night<br>Emergency Water<br>Damage Cleanup</div>
      <div class="phone">404-555-0182</div>
      <div class="web">www.tovincrest.com</div>
    </div>
  </section>

  <section class="panel cover">
    <div class="cover-photo" role="img" aria-label="Photo of a technician in protective gear treating mold in a crawl space"></div>
    <svg class="cover-band" viewBox="0 0 283 656" preserveAspectRatio="none" aria-hidden="true">
      <polygon points="0,345 283,300 283,480 0,520" fill="#2360c4"/>
      <polygon points="40,500 283,330 283,474" fill="#163f8a"/>
      <polygon points="0,520 283,480 283,488 0,530" fill="#d3232a"/>
    </svg>
    <div class="cover-title">Water, Flood Fire<br>Mold Damage<br>Restoration</div>
    <div class="brand">
      <div class="brand-name"><span class="brand-mark"></span>Tovin Crest</div>
      <div class="brand-tag">Water Damage Specialists</div>
      <div class="brand-web">www.tovincrest.com</div>
    </div>
  </section>

</main>
</body>
</html>
```